Web design for business website

I need a web design for a business website for one of our clients who is specialized in alarm management software. I would like you to design 3 web pages, one for each of the 3 pages. You need to process the corporate identity of our client to the web design. This means the colors of the logo (red and black) should definitely show up on all of the 3 pages. Find the logo file for the logo of our customer. To increase readability I suggest you use a white/light background. All suggestions are welcome.

Please kindly download atttached Webdesign.zip and read the project brief first. The project brief refers to all other files of the zip file. Your design must have exactly the same structure as the wireframes.
Updates

Target Market(s)

B2B, Alarm management

Industry/Entity Type

Business

Number of Pages Required

3 page

Requirements
Must have
• The web design must have exactly the same structure as the wireframes and needs to contain the colors of the company logo.

```html
<!DOCTYPE html>
<html lang="en">
<head>
<meta charset="utf-8">
<title>Arvelon – Live alarm insight software</title>
<link rel="stylesheet" href="https://fonts.googleapis.com/css2?family=Lato:ital,wght@0,400;0,700;0,900;1,400;1,700&family=Roboto:wght@400;500;700&display=swap">
<style>
:root{
  --red:#e8381a;
  --ink:#1b1b1b;
  --text:#333;
  --muted:#666;
  --line:#d9d9d9;
  --panel:#f3f3f3;
  --white:#fff;
  --black:#000;
}
*{box-sizing:border-box;margin:0;padding:0}
html,body{width:1200px;height:1098px;overflow:hidden;background:var(--white)}
body{position:relative;font-family:Lato,Arial,sans-serif;color:var(--text)}
.abs{position:absolute}

/* header */
.brand{left:130px;top:24px;display:flex;align-items:center;gap:14px}
.brand-mark{width:22px;height:22px;background:var(--ink)}
.brand-name{font:700 36px/1 Lato,sans-serif;color:var(--ink)}
.brand-tag{font:400 13.5px Lato,sans-serif;color:var(--muted);margin-top:6px;letter-spacing:.3px}
.top-phone{left:622px;top:13px;display:flex;align-items:center;gap:10px;font:700 17px Roboto,sans-serif;color:var(--ink)}
.lang{left:818px;top:11px;width:84px;height:25px;border:1px solid #ccc;font-size:13px;color:#999;padding:3px 10px;display:flex;justify-content:space-between}
.search{left:910px;top:11px;width:159px;height:25px;border:1px solid #ccc;display:flex}
.search span{flex:1;font:italic 13px Lato,sans-serif;color:#999;padding:4px 8px}
.search b{width:26px;background:var(--ink);display:flex;align-items:center;justify-content:center}
.user-links{right:131px;top:58px;display:flex;gap:24px;font:400 15px Lato,sans-serif;color:var(--ink)}
.user-links span{display:flex;align-items:center;gap:8px}
.main-nav{left:130px;top:111px;width:939px;display:flex;justify-content:space-between;font:700 15px Lato,sans-serif;letter-spacing:.3px;color:var(--ink)}
.main-nav i{width:1px;height:16px;background:#ddd}
.main-nav .active{color:var(--red)}

/* intro */
.intro{left:131px;top:165px;width:660px;font-size:15.5px;line-height:22.5px;letter-spacing:.4px;color:#333;white-space:nowrap}
.intro p{margin-bottom:10px}

/* form */
.contact-form{left:131px;top:408px;width:634px;height:143px;border-radius:10px;background:#eee;padding:4px}
.contact-form .inner{width:100%;height:100%;border:1px solid #ccc;border-radius:9px;background:var(--panel);position:relative}
.field{position:absolute;background:#fff;border:1px solid #ccc;box-shadow:inset 0 1px 2px rgba(0,0,0,.1);font-size:12.5px;color:#555;padding:4px 12px}
.send{position:absolute;left:324px;top:87px;width:96px;height:25px;background:var(--red);color:#fff;font:700 14px Lato,sans-serif;text-align:center;line-height:25px}

/* clients */
.clients-tab{left:340px;top:594px;width:219px;height:51px;border:1px solid #ccc;border-bottom:none;background:#fff;font:700 29px Roboto,sans-serif;color:var(--black);text-align:center;line-height:56px;z-index:2}
.clients-tab em{font-style:normal;color:var(--red)}
.clients-box{left:131px;top:643px;width:634px;height:100px;border:1px solid #ccc;border-radius:0 0 6px 6px;display:flex;align-items:center;justify-content:space-around;padding:0 40px}
.client{display:flex;align-items:center;gap:6px;font:700 17px Lato,sans-serif;color:#555}
.client i{width:14px;height:14px;border-radius:50%;background:#bbb}
.arrow{top:678px;width:30px;height:30px}

/* sidebar */
.video{left:806px;top:169px;width:263px;height:170px;background:linear-gradient(180deg,#e9a34a 0%,#c98b52 35%,#8d8a86 70%,#6f7275 100%)}
.video-bar{left:806px;top:321px;width:263px;height:18px;background:linear-gradient(#3a4452,#1c232c)}
.video-shadow{left:816px;top:340px;width:243px;height:8px;background:radial-gradient(ellipse at top,rgba(0,0,0,.25),transparent 70%)}
.section-title{left:806px;top:370px;width:263px;height:36px;border-bottom:1px solid #eee;display:flex;align-items:center;gap:12px;font:700 24px Roboto,sans-serif;color:var(--black)}
.avatar{left:807px;top:414px;width:88px;height:88px;border-radius:50%;border:3px solid #1d2530;background:radial-gradient(circle at 50% 45%,#d8b49a,#8a7062 60%,#5a5250)}
.person{left:909px;top:440px;font-size:15px;font-weight:700;color:var(--red)}
.person span{display:block;font-weight:400;font-size:13.5px;color:#444;margin-top:4px}
.quote{left:806px;top:517px;width:263px;height:89px;border:1px solid #e4e4e4;padding:9px 13px;font:italic 14px/22.5px Lato,sans-serif;color:#444}
.quote-notch{left:900px;top:507px;width:18px;height:18px;background:#fff;border-left:1px solid #e4e4e4;border-top:1px solid #e4e4e4;transform:rotate(45deg) skew(8deg,8deg)}
.q{font-family:Georgia,serif;font-size:30px;color:#ccc;line-height:0;vertical-align:-10px}
.call-box{left:806px;top:636px;width:263px;height:107px;background:#d9edf6;border:1px solid #cfe3ee}
.call-photo{left:806px;top:636px;width:118px;height:107px;background:linear-gradient(90deg,#c8b09a,#e6d4c4 60%,#d9edf6)}
.call-text{left:924px;top:648px;width:140px;text-align:center;font:700 13.5px Roboto,sans-serif;color:var(--black)}
.call-text strong{display:block;font-size:15px;color:var(--red);margin-top:4px}

/* footer band */
.band{left:0;top:780px;width:1200px;height:56px;background:var(--black);border-top:2px solid #333}
.follow{left:130px;top:796px;font:italic 700 21px Lato,sans-serif;color:#fff}
.social{top:792px;width:33px;height:33px;border-radius:50%}
.news-icon{left:490px;top:784px;width:50px;height:50px;border-radius:50%;border:2px solid #fff;display:flex;align-items:center;justify-content:center}
.news-title{left:550px;top:797px;font:400 19px Roboto,sans-serif;color:#fff}
.news-underline{left:551px;top:821px;width:58px;height:2px;background:var(--red)}
.news-input{left:718px;top:795px;width:252px;height:30px;background:#fff;border-radius:2px;font:italic 13px Lato,sans-serif;color:#555;padding:7px 9px}
.subscribe{left:979px;top:795px;width:90px;height:29px;background:var(--red);color:#fff;font:700 13px Lato,sans-serif;text-align:center;line-height:29px;border-radius:2px}

/* footer columns */
.col{top:863px}
.col h3{font:400 17.5px Lato,sans-serif;color:var(--ink);letter-spacing:.3px;padding-bottom:8px;border-bottom:1px dotted #ccc;width:126px}
.col ul{list-style:none;margin-top:12px}
.col li{font-size:12.5px;color:#333;height:29.3px;padding-left:17px;position:relative}
.col li::before{content:"›";position:absolute;left:2px;top:-2px;color:#888;font-size:13px}
.contact-col{left:886px;top:863px;width:183px}
.contact-col h3{width:183px}
.contact-row{display:flex;gap:12px;font-size:13.5px;color:#333;line-height:18px;margin-top:8px}
.contact-row svg{flex:none;margin-top:2px}
.offices{margin:8px 0 0 32px;font:700 13.5px Lato,sans-serif;color:var(--ink);text-decoration:underline}
.legal{left:0;top:1061px;width:1200px;height:37px;background:var(--red);color:#fff;font:700 12.5px Lato,sans-serif;text-align:center;line-height:33px;letter-spacing:.3px}
</style>
</head>
<body>

<header>
  <div class="abs brand">
    <div class="brand-mark"></div>
    <div>
      <div class="brand-name">Arvelon</div>
      <div class="brand-tag">Live alarm insight software</div>
    </div>
  </div>
  <div class="abs top-phone">
    <svg width="20" height="20" viewBox="0 0 24 24"><path fill="#e8381a" d="M6.6 10.8a15.1 15.1 0 0 0 6.6 6.6l2.2-2.2c.3-.3.7-.4 1-.2 1.1.4 2.3.6 3.6.6.6 0 1 .4 1 1V20c0 .6-.4 1-1 1A17 17 0 0 1 3 4c0-.6.4-1 1-1h3.5c.6 0 1 .4 1 1 0 1.3.2 2.5.6 3.6.1.3 0 .7-.2 1z"/></svg>
    +31 (0)20 555 0147
  </div>
  <div class="abs lang">English <span>⌄</span></div>
  <div class="abs search"><span>Search</span><b><svg width="13" height="13" viewBox="0 0 14 14"><circle cx="6" cy="6" r="4.3" stroke="#fff" stroke-width="2" fill="none"/><path d="M9.2 9.2 13 13" stroke="#fff" stroke-width="2"/></svg></b></div>
  <div class="abs user-links">
    <span><svg width="24" height="22" viewBox="0 0 24 22"><circle cx="12" cy="6" r="5" fill="#e8381a"/><path d="M1 22c1-7 5-9 11-9s10 2 11 9z" fill="#e8381a"/></svg>Account</span>
    <span><svg width="18" height="22" viewBox="0 0 18 22"><path d="M4 9V6a5 5 0 0 1 10 0v3" stroke="#e8381a" stroke-width="2.5" fill="none"/><rect x="1" y="9" width="16" height="13" rx="2" fill="#e8381a"/><rect x="8" y="13" width="2" height="5" fill="#fff"/></svg>Log in</span>
    <span><svg width="24" height="22" viewBox="0 0 24 22"><circle cx="10" cy="6" r="5" fill="#e8381a"/><path d="M0 21c1-7 4-8 10-8s7 1 8 3" fill="#e8381a"/><circle cx="18" cy="17" r="5" fill="#e8381a"/><path d="M18 14v6M15 17h6" stroke="#fff" stroke-width="1.6"/></svg>Sign up</span>
  </div>
  <nav class="abs main-nav">
    <span>HOME</span><i></i><span class="active">INDUSTRY</span><i></i><span>TELECOM</span><i></i><span>POWER</span><i></i><span>UTILITIES</span><i></i><span>INFRA</span><i></i><span>STORE</span>
  </nav>
</header>

<main>
  <section class="abs intro">
    <p>Dynamisch Engagement Van Bedrijfsmeta-services Voor Door De Markt Gestimuleerde<br>Gegevens. Samenwerkend Herstel Van Gebruikers Over Verschillende Platforms Vóór Op<br>Klant Gerichte Vervaardigde Producten.</p>
    <p>Overtuigende Ontwikkeling Van Verticale Portalen Op Lange Termijn Met Hoge Impact Via<br>Visionaire Oplossingen. Professionele Aanwending Van Gestandaardiseerde Portalen Ten<br>Opzichte Van Te Leveren Producten Die De Bronnen Maximaliseren.</p>
    <p>Dynamische Optimalisatie Volledig Onderzochte Resultaten Voor Onafhankelijk Menselijke<br>Kapitaal. Complete Overheersing Van Naadloze Synergie Via Interoperabele Methodologieën.</p>
  </section>

  <form class="abs contact-form">
    <div class="inner">
      <div class="field" style="left:19px;top:19px;width:282px;height:25px">Name</div>
      <div class="field" style="left:19px;top:53px;width:282px;height:25px">Email</div>
      <div class="field" style="left:19px;top:87px;width:282px;height:25px">Telephone</div>
      <div class="field" style="left:324px;top:19px;width:282px;height:60px">Comment</div>
      <div class="send">SEND</div>
    </div>
  </form>

  <div class="abs clients-tab">Clients <em>Using</em></div>
  <section class="abs clients-box">
    <span class="client"><i></i>Fenwyk</span>
    <span class="client"><i></i>Dunmere</span>
    <span class="client"><i></i>Calvorn</span>
    <span class="client"><i></i>Tessaly</span>
    <span class="client"><i></i>Brynmoor Oil</span>
  </section>
  <svg class="abs arrow" style="left:115px" viewBox="0 0 30 30"><rect x="5" y="5" width="20" height="20" transform="rotate(45 15 15)" fill="#1b1b1b"/><path d="M17 10l-5 5 5 5" stroke="#fff" stroke-width="2.4" fill="none"/></svg>
  <svg class="abs arrow" style="left:749px" viewBox="0 0 30 30"><rect x="5" y="5" width="20" height="20" transform="rotate(45 15 15)" fill="#1b1b1b"/><path d="M13 10l5 5-5 5" stroke="#fff" stroke-width="2.4" fill="none"/></svg>

  <aside>
    <div class="abs video" role="img" aria-label="Video still of a city highway interchange at sunset"></div>
    <svg class="abs" style="left:916px;top:226px" width="40" height="44" viewBox="0 0 40 44"><path d="M2 2l36 20-36 20z" fill="rgba(255,255,255,.55)"/></svg>
    <div class="abs video-bar">
      <svg width="263" height="18" viewBox="0 0 263 18"><rect x="6" y="4" width="15" height="10" rx="2" fill="#4d6fa8"/><path d="M11 6l5 3-5 3z" fill="#fff"/><rect x="33" y="7" width="125" height="4" rx="2" fill="#ddd"/><rect x="33" y="7" width="28" height="4" rx="2" fill="#6b8fd0"/><rect x="203" y="4" width="14" height="10" rx="2" fill="#4d6fa8"/><rect x="223" y="4" width="14" height="10" rx="2" fill="#4d6fa8"/><rect x="242" y="4" width="14" height="10" rx="2" fill="#4d6fa8"/></svg>
    </div>
    <div class="abs video-shadow"></div>

    <div class="abs section-title">
      <svg width="32" height="30" viewBox="0 0 32 30"><path d="M2 2h20v13H10l-5 5v-5H2z" fill="#e8381a"/><path d="M12 12h18v13h-3v5l-5-5H12z" fill="#e8381a" stroke="#fff" stroke-width="1.5"/><circle cx="17" cy="18.5" r="1.4" fill="#fff"/><circle cx="21" cy="18.5" r="1.4" fill="#fff"/><circle cx="25" cy="18.5" r="1.4" fill="#fff"/></svg>
      Testimonials
    </div>
    <div class="abs avatar" role="img" aria-label="Portrait photo of the client"></div>
    <div class="abs person">Marco Velden<span>Bussiness Man</span></div>
    <div class="abs quote-notch"></div>
    <blockquote class="abs quote"><span class="q">“</span> Ut wisi enim ad minim veniam, quism nostrli erci tation ullamcorper suscipitop lobortis commodo consequat. <span class="q">”</span></blockquote>

    <div class="abs call-box"></div>
    <div class="abs call-photo" role="img" aria-label="Photo of a smiling support agent with a headset"></div>
    <div class="abs call-text">
      <svg width="30" height="30" viewBox="0 0 30 30"><circle cx="15" cy="15" r="13" stroke="#e8381a" stroke-width="2" fill="none"/><path d="M10.5 12.8a10 10 0 0 0 6.7 6.7l1.6-1.6c.2-.2.5-.3.7-.1.8.3 1.6.4 2.4.4v2.6c0 .4-.3.7-.7.7A12 12 0 0 1 8 9.7c0-.4.3-.7.7-.7h2.6c0 .8.1 1.6.4 2.4 0 .3 0 .5-.2.7z" fill="#e8381a"/></svg>
      <div style="margin-top:2px">Call Us Today</div>
      <strong>+31 (0)20 555 0147</strong>
    </div>
  </aside>
</main>

<footer>
  <div class="abs band"></div>
  <div class="abs follow">Follow Us</div>
  <div class="abs social" style="left:229px;background:#29a9d8"></div>
  <div class="abs social" style="left:274px;background:#d8251f"></div>
  <div class="abs social" style="left:320px;background:#2a7fd0"></div>
  <div class="abs news-icon"><svg width="26" height="26" viewBox="0 0 26 26"><circle cx="13" cy="13" r="13" fill="#e8381a"/><rect x="6" y="8" width="14" height="10" fill="#fff"/><path d="M6 8l7 6 7-6" stroke="#e8381a" stroke-width="1.3" fill="none"/></svg></div>
  <div class="abs news-title">Newsletter Signup</div>
  <div class="abs news-underline"></div>
  <div class="abs news-input">Email Address</div>
  <div class="abs subscribe">SUBSCRIBE</div>

  <div class="abs col" style="left:132px"><h3>SOLUTIONS</h3><ul><li>Vigil Alarm Reporting</li><li>Vigil Alarm Analysis</li><li>Vigil Alarm Expert</li><li>USE</li></ul></div>
  <div class="abs col" style="left:332px"><h3>INDUSTRIES</h3><ul><li>Industry</li><li>Telecom</li><li>Power</li><li>Utilities</li><li>Infra</li></ul></div>
  <div class="abs col" style="left:516px"><h3>ABOUT US</h3><ul><li>Company</li><li>Overview</li><li>Leadership</li><li>Partners</li><li>Locations</li></ul></div>
  <div class="abs col" style="left:699px"><h3>NEWS</h3><ul><li>Product News</li><li>Partner News</li><li>Events</li><li>Press Releases</li><li>Vacancies</li></ul></div>
  <div class="abs col contact-col">
    <h3>CONTACT DETAILS</h3>
    <div class="contact-row"><svg width="18" height="18" viewBox="0 0 18 18"><path d="M9 1a6 6 0 0 1 6 6c0 4-6 10-6 10S3 11 3 7a6 6 0 0 1 6-6z" fill="#e8381a"/><circle cx="9" cy="7" r="2.2" fill="#fff"/></svg><span>Arvelon,<br>Lindenkade 24,<br>1015 AB Amsterdam</span></div>
    <div class="contact-row"><svg width="18" height="16" viewBox="0 0 24 24"><path fill="#e8381a" d="M6.6 10.8a15.1 15.1 0 0 0 6.6 6.6l2.2-2.2c.3-.3.7-.4 1-.2 1.1.4 2.3.6 3.6.6.6 0 1 .4 1 1V20c0 .6-.4 1-1 1A17 17 0 0 1 3 4c0-.6.4-1 1-1h3.5c.6 0 1 .4 1 1 0 1.3.2 2.5.6 3.6.1.3 0 .7-.2 1z"/></svg><span>+31 (0)20 555 0147</span></div>
    <div class="contact-row"><svg width="18" height="14" viewBox="0 0 18 14"><rect x="1" y="2" width="16" height="10" fill="#e8381a"/><path d="M1 2l8 6 8-6" stroke="#fff" stroke-width="1.4" fill="none"/></svg><span>hello@arvelon.com</span></div>
    <div class="offices">OTHER OFFICES</div>
  </div>
  <div class="abs legal">© 2015 &nbsp;Arvelon. All Right Reserved.</div>
</footer>

</body>
</html>
```